Business Card for Professional Photographer

I'm looking for an eye catching modern clean design that compliments my logo/ website fonts & colours.
I specialise in architecture, corporate & commercial photography so I'm marketing to professional clients rather than portrait / wedding clients.

I would prefer to not have a solid black design.

My logo brand guide is as follows :

Main front font. : Reislust
Main font colour : #fff
Slogan front font : Ubuntu Bold
Monogram front font : Venti Medium
Container colour : #fff

I need print ready files in pdf .png & .eps formats.

Included in the files below are some screen grabs as reference to font & colours etc.

```html
<!DOCTYPE html>
<html lang="en">
<head>
<meta charset="utf-8">
<title>Brightline Studio – Business Card</title>
<link rel="stylesheet" href="https://fonts.googleapis.com/css2?family=Ubuntu:wght@500;700&family=Roboto:wght@400&family=Barlow+Condensed:wght@600&display=swap">
<style>
  :root {
    --backdrop: #b4b4b4;
    --gold-light: #e6dc9c;
    --gold-mid: #d3b46e;
    --gold-deep: #b98f4a;
    --gold-ink: #a97a3c;
    --card-white: #f7f7f6;
    --ink: #1a1a1a;
    --text-grey: #3b3b3b;
  }
  * { margin: 0; padding: 0; box-sizing: border-box; }
  html, body {
    width: 1200px; height: 576px; overflow: hidden;
    background: var(--backdrop);
  }
  .canvas { position: relative; width: 1200px; height: 576px; }

  .card {
    position: absolute;
    top: 138px;
    height: 294px;
    border-radius: 10px;
    box-shadow: 0 3px 6px rgba(0,0,0,0.25);
    overflow: hidden;
  }

  /* Front */
  .card-front {
    left: 80px; width: 486px;
    background: linear-gradient(115deg, var(--gold-deep) 0%, var(--gold-mid) 45%, var(--gold-light) 100%);
  }
  .front-lockup {
    position: absolute; left: 0; right: 0; top: 116px;
    text-align: center;
  }
  .brand-name {
    font-family: "Ubuntu", sans-serif;
    font-weight: 500;
    letter-spacing: 0.5px;
    white-space: nowrap;
  }
  .front-lockup .brand-name { font-size: 26px; color: var(--ink); }
  .tagline {
    font-family: "Ubuntu", sans-serif;
    font-weight: 700;
    font-size: 9px;
    letter-spacing: 1px;
    text-transform: uppercase;
    white-space: nowrap;
  }
  .front-lockup .tagline { color: var(--ink); margin-top: 5px; }
  .front-web {
    position: absolute; left: 0; right: 0; top: 256px;
    text-align: center;
    font-family: "Roboto", sans-serif;
    font-size: 13px;
    letter-spacing: 2px;
    color: var(--ink);
  }

  /* Back */
  .card-back {
    left: 602px; width: 482px;
    background: var(--card-white);
  }
  .back-brand { position: absolute; left: 30px; top: 32px; }
  .back-brand .brand-name { font-size: 24px; color: var(--gold-ink); }
  .back-brand .tagline { color: var(--gold-ink); margin-top: 4px; }

  .person { position: absolute; left: 25px; top: 134px; }
  .person-name {
    font-family: "Barlow Condensed", sans-serif;
    font-weight: 600;
    font-size: 20px;
    color: var(--gold-ink);
  }
  .person-role {
    font-family: "Roboto", sans-serif;
    font-size: 13px;
    color: var(--text-grey);
    margin-top: 1px;
  }

  .contact-list {
    position: absolute; left: 25px; top: 194px;
    list-style: none;
    font-family: "Roboto", sans-serif;
    font-size: 13px;
    color: var(--text-grey);
  }
  .contact-list li { display: flex; align-items: center; height: 18.5px; }
  .contact-icon { width: 11px; height: 11px; margin: 0 13px 0 5px; fill: var(--gold-mid); }
  .contact-address { margin-top: 10px; }
</style>
</head>
<body>
<div class="canvas">

  <section class="card card-front">
    <div class="front-lockup">
      <div class="brand-name">BRIGHTLINE STUDIO</div>
      <div class="tagline">Buildings · Business · Brands</div>
    </div>
    <div class="front-web">www.brightlinestudio.com.au</div>
  </section>

  <section class="card card-back">
    <div class="back-brand">
      <div class="brand-name">BRIGHTLINE STUDIO</div>
      <div class="tagline">Buildings · Business · Brands</div>
    </div>

    <div class="person">
      <div class="person-name">Marcus Hale</div>
      <div class="person-role">Photographer</div>
    </div>

    <ul class="contact-list">
      <li>
        <svg class="contact-icon" viewBox="0 0 12 12" aria-hidden="true"><path d="M1 3c0-1.5 1.5-2 5-2s5 .5 5 2v1H8.5V3h-5v1H1z M2.5 5h7l1.5 6H1z"/></svg>
        0400555128
      </li>
      <li>
        <svg class="contact-icon" viewBox="0 0 12 12" aria-hidden="true"><path d="M0 2h12v8H0z M1 3v.4l5 3.3 5-3.3V3z" fill-rule="evenodd"/></svg>
        info@brightlinestudio.com.au
      </li>
      <li>
        <svg class="contact-icon" viewBox="0 0 12 12" aria-hidden="true"><circle cx="6" cy="6" r="5.5"/><path d="M.5 6h11M6 .5v11" stroke="#f7f7f6" stroke-width="0.9"/></svg>
        www.brightlinestudio.com.au
      </li>
      <li class="contact-address">48 Harbour Rd Westmere Vic 3351</li>
    </ul>
  </section>

</div>
</body>
</html>
```